New Business Card Design for Manufacturing

We are an engineering/manufacturing company that offers Advanced machining/assembly/engineering services, as well as innovative products for the heavy duty engine cooling markets.

We are looking to get a new business card designed that is clean and modern looking, but still fits the wide range of technical/skilled work we do.

- We hope to use this design as the base for other design work in new Presentations, web, and print work.

Industry/Entity Type

Engineering

Contact Information for Business Card

Our preferred color of blue is (RGB) 22/71/159 but can vary slightly from that color. Our content will be our Logo and full company name (Vantrell Forge Works, Inc.), company address, name, job title, phone number with extension, cell number, fax number, website, and email address on the cards.
We'd like the full company name next to the logo, but we are open to other interpretations of that layout.
Preferably, we would like the back side to be clean with just our logo, and the front to contain all of the contact information.

Colors
2f74b4
0355a3
85abd2

Requirements
Must have
• - Logo, company name, needed content - We are open to interpretation beyond that.
• - Standard size business card.
• - Horizontal orientation.
• - Enough space for lengthy names / job titles (for example, a job title could read "Directory of Human Resources" or "V.P. of Governmental Affairs"). We need this to look clean, whether the title be short (CEO) or long (as described above).

```html
<!DOCTYPE html>
<html lang="en">
<head>
<meta charset="utf-8">
<title>Vantrell Forge Works – Business Card</title>
<link rel="stylesheet" href="https://fonts.googleapis.com/css2?family=Arimo:wght@400;700&display=swap">
<style>
  :root {
    --backdrop: #9a9a9a;
    --card-white: #ffffff;
    --brand-blue: #0d4ea3;
    --back-blue: #0e4f9f;
    --ink: #2a2a2a;
    --muted-grey: #7a7a7a;
    --rule: #9c9c9c;
  }
  * { box-sizing: border-box; margin: 0; padding: 0; }
  html, body {
    width: 1200px; height: 900px; overflow: hidden;
    background: var(--backdrop);
    font-family: "Arimo", Arial, sans-serif;
  }
  .stage { position: relative; width: 1200px; height: 900px; }
  .card {
    position: absolute; top: 306px; width: 439px; height: 271px;
    border-radius: 12px;
    box-shadow: 2px 3px 4px rgba(0,0,0,0.45);
  }
  .card-front { left: 149px; background: var(--card-white); }
  .card-back { left: 608px; background: var(--back-blue); overflow: hidden; }

  .brand-lockup { position: absolute; left: 31px; top: 100px; width: 192px; }
  .brand-name {
    display: block; font-weight: 700; font-size: 37px; line-height: 1;
    color: var(--brand-blue); letter-spacing: 0.5px;
  }
  .brand-tagline {
    display: block; margin-top: 9px; font-weight: 700; font-size: 11.5px;
    color: var(--muted-grey); letter-spacing: 0.1px;
  }

  .divider {
    position: absolute; left: 241px; top: 57px; width: 1px; height: 154px;
    background: var(--rule);
  }

  .contact-block { position: absolute; left: 255px; top: 57px; color: var(--ink); }
  .person-name {
    font-weight: 700; font-size: 16.5px; color: var(--brand-blue);
    line-height: 18px; letter-spacing: 0.2px;
  }
  .person-title { font-size: 11px; line-height: 13px; letter-spacing: 0.2px; margin-top: 1px; }
  .contact-list { list-style: none; margin-top: 11px; }
  .contact-list li {
    display: flex; align-items: center; gap: 5px;
    font-size: 12.5px; line-height: 16px;
  }
  .contact-icon { width: 9px; height: 9px; fill: var(--brand-blue); flex: none; }
  .address { margin-top: 8px; font-size: 12.5px; line-height: 16px; }

  .back-texture { position: absolute; inset: 0; background: var(--back-blue); }
  .back-mark {
    position: absolute; left: 0; right: 0; top: 122px; text-align: center;
    font-weight: 700; font-size: 20px; line-height: 24px; color: var(--card-white);
    letter-spacing: 0.5px;
  }
</style>
</head>
<body>
<main class="stage">
  <section class="card card-front" aria-label="Business card front">
    <div class="brand-lockup">
      <span class="brand-name">VANTRELL</span>
      <span class="brand-tagline">POWERING THE FUTURE</span>
    </div>
    <div class="divider"></div>
    <div class="contact-block">
      <p class="person-name">MARCUS ELLERY</p>
      <p class="person-title">MANAGING DIRECTOR</p>
      <ul class="contact-list">
        <li><svg class="contact-icon" viewBox="0 0 10 10"><path d="M1 3 Q5 0 9 3 L8 4.5 L6.5 3.8 L6.5 3 Q5 2.5 3.5 3 L3.5 3.8 L2 4.5 Z M2.5 5 H7.5 L8.5 9 H1.5 Z"/></svg>(044)123456789</li>
        <li><svg class="contact-icon" viewBox="0 0 10 10"><path d="M2.8 0.5 H7.2 V9.5 H2.8 Z M3.6 1.5 V7.8 H6.4 V1.5 Z"/></svg>(044)123456789</li>
        <li><svg class="contact-icon" viewBox="0 0 10 10"><path d="M3 0.5 H7 V3.5 H3 Z M1 3.5 H9 V9.5 H1 Z M3 5 V6 H7 V5 Z"/></svg>(044)123456789</li>
        <li><svg class="contact-icon" viewBox="0 0 10 10"><path d="M0.5 2 H9.5 V8.5 H0.5 Z" /><path d="M0.8 2.3 L5 5.6 L9.2 2.3" stroke="#fff" stroke-width="0.9" fill="none"/></svg>info@youremail.com</li>
        <li><svg class="contact-icon" viewBox="0 0 10 10"><circle cx="5" cy="5" r="4.5"/><path d="M3 3 Q5 2 6 4 Q5 6 7 7" stroke="#fff" stroke-width="0.9" fill="none"/></svg>www.websitename.com</li>
      </ul>
      <p class="address">1234, Address GoesHere,<br>Country name, 12345</p>
    </div>
  </section>

  <section class="card card-back" aria-label="Business card back">
    <div class="back-texture" role="img" aria-label="Faint repeated brand pattern on blue"></div>
    <p class="back-mark">VANTRELL</p>
  </section>
</main>
</body>
</html>
```